Software Development Consulting Company Needs Business Card Design

We need a new business card design for our consultants at Kestrel Works (kestrelworks.example). We are a small firm that provides high-end software development and methodology consulting to medium to large enterprise IT organizations.

Our logo uses Futura for the font and we would like to stick with navy blue and canary yellow for the logo colors. Attached are normal and reversed versions of our logos in illustrator format.
Updates

Hi Everyone, Thank yo very much for your amazing design ideas. I have created a poll for this project and our employees will be voting on the design they wish to use. We will be making a decision this Wednesday (October 22nd). Thanks again, Dale Hartwick

Industry/Entity Type

Business

```html
<!DOCTYPE html>
<html lang="en">
<head>
<meta charset="utf-8">
<title>Kestrel Works — Business Card</title>
<link rel="stylesheet" href="https://fonts.googleapis.com/css2?family=Jost:wght@400;500;600&display=swap">
<style>
  :root {
    --navy: #1d4a70;
    --canary: #f5ea12;
    --white: #ffffff;
    --grey-text: #8a8f96;
    --backdrop: #e9eaee;
    --card-shadow: rgba(20, 30, 50, 0.22);
  }
  * { margin: 0; padding: 0; box-sizing: border-box; }
  html, body {
    width: 1200px; height: 980px; overflow: hidden;
    background: var(--backdrop);
    font-family: "Jost", sans-serif;
  }
  .canvas { position: relative; width: 1200px; height: 980px; }
  .card {
    position: absolute; left: 290px; width: 620px; height: 354px;
    border-radius: 22px; overflow: hidden;
    box-shadow: 0 10px 30px var(--card-shadow);
  }
  .card--front { top: 90px; background: var(--white); }
  .card--back { top: 530px; background: var(--navy); }
  .card__art { position: absolute; inset: 0; width: 100%; height: 100%; }

  .brand { position: absolute; display: flex; align-items: center; gap: 12px; }
  .brand__dot { width: 16px; height: 16px; border-radius: 50%; background: var(--canary); }
  .brand__name { font-weight: 500; font-size: 30px; letter-spacing: 4px; text-transform: uppercase; line-height: 1; }
  .card--front .brand { left: 44px; top: 44px; }
  .card--front .brand__name { color: var(--navy); }
  .card--back .brand { left: 50%; top: 130px; transform: translateX(-50%); }
  .card--back .brand__name { color: var(--white); font-size: 34px; }

  .person { position: absolute; left: 62px; top: 102px; }
  .person__name { color: var(--navy); font-weight: 600; font-size: 21px; }
  .person__title { color: var(--grey-text); font-size: 14px; margin-top: 2px; }

  .address { position: absolute; left: 26px; bottom: 20px; color: var(--white); font-size: 15px; }
  .contact { position: absolute; left: 330px; top: 262px; list-style: none; color: var(--white); font-size: 15px; }
  .contact__item { display: flex; align-items: center; gap: 8px; height: 25px; }
  .contact__icon { width: 15px; height: 15px; flex: none; }

  .web-address {
    position: absolute; left: 0; right: 0; top: 205px; text-align: center;
    color: var(--white); font-size: 18px; letter-spacing: 3px;
  }
</style>
</head>
<body>
<main class="canvas">

  <section class="card card--front" aria-label="Business card front">
    <svg class="card__art" viewBox="0 0 620 354" aria-hidden="true">
      <path d="M0,100 C10,200 50,225 220,232 C400,240 540,250 620,300 V354 H0 Z" fill="var(--navy)"/>
      <path d="M-2,92 C6,196 46,216 220,222 C400,230 540,240 622,290" fill="none" stroke="var(--canary)" stroke-width="5"/>
      <path d="M-2,84 C4,190 44,208 220,213 C400,220 540,230 622,280" fill="none" stroke="var(--navy)" stroke-width="1.5"/>
    </svg>

    <div class="brand">
      <span class="brand__dot"></span>
      <span class="brand__name">Kestrel Works</span>
    </div>

    <div class="person">
      <p class="person__name">Your Name</p>
      <p class="person__title">Title</p>
    </div>

    <p class="address">Ridgeview + Maple Falls, IL</p>

    <ul class="contact">
      <li class="contact__item">
        <svg class="contact__icon" viewBox="0 0 16 16" aria-hidden="true"><circle cx="8" cy="8" r="7" fill="none" stroke="#fff" stroke-width="1.3"/><path d="M5.5 4.5l1.5 1.5-1 1a5 5 0 0 0 3 3l1-1 1.5 1.5-1.2 1.2C7.5 11.5 4.5 8.5 4.3 5.7z" fill="#fff"/></svg>
        012-555-0148
      </li>
      <li class="contact__item">
        <svg class="contact__icon" viewBox="0 0 16 16" aria-hidden="true"><rect x="1.5" y="3.5" width="13" height="9" rx="1" fill="none" stroke="#fff" stroke-width="1.3"/><path d="M2 4l6 5 6-5" fill="none" stroke="#fff" stroke-width="1.3"/></svg>
        info@kestrelworks.example
      </li>
      <li class="contact__item">
        <svg class="contact__icon" viewBox="0 0 16 16" aria-hidden="true"><circle cx="8" cy="8" r="7" fill="none" stroke="#fff" stroke-width="1.3"/><ellipse cx="8" cy="8" rx="3" ry="7" fill="none" stroke="#fff" stroke-width="1.1"/><path d="M1 8h14M2.5 4.5h11M2.5 11.5h11" stroke="#fff" stroke-width="1"/></svg>
        www.kestrelworks.example
      </li>
    </ul>
  </section>

  <section class="card card--back" aria-label="Business card back">
    <div class="brand">
      <span class="brand__dot"></span>
      <span class="brand__name">Kestrel Works</span>
    </div>
    <p class="web-address">www.kestrelworks.example</p>
  </section>

</main>
</body>
</html>
```